NZ First of it's kind solutions directory and marketplace for busy Mums needs a business card design

We need a business card design for our new nationwide business in NZ (long term plans to go global). We provide solutions to the everyday challenges that busy Mums face by connecting them with quality communities and suppliers of carefully selected, relevant products and services. We sell direct via our online marketplace. The final design should communicate our values of inclusivity, quality and smart solutions. Colours should incorporate our logo colour palette of #477077 and #6ba8b2. Our website is at https://www.brightnestmums.example

Target Market(s)

busy Mums, Age 28 – 50, female, income over $100K, location main centres NZ primarily but NZ wide. Is likely juggling work or career with a young family. Probably had hobbies which have fallen by the wayside.
-Wants to succeed in her chosen career without compromising on family life
-to successfully juggle her career without feeling like she is compromising her children
- Is time poor, something always has to give and it’s generally her health (she’ll stay up late, get stressed)
- probably ex corporate or professional career. Has discretional income

Industry/Entity Type

Business

Contact Information for Business Card

Lena Forbisher, Founder, BrightNestMums.example (Strapline Tap; Gather; Sorted), 47 Kowhai Terrace, Ellerslie, Auckland 1051, New Zealand. Mob: 021 483 517 Ph: +64 (0)9 571 4860

Font styles to use
Other font styles liked:
• Raleway, and/or Architects Daughter

Colors
00a990
33b8a4
86cfc6
cfeae6

Requirements
Must have
• the above details, streamline. the logo and colours associated with those logos
Should not have
• foil or metallic colours

```html
<!DOCTYPE html>
<html lang="en">
<head>
<meta charset="utf-8">
<title>BrightNestMums – Business Card</title>
<link rel="stylesheet" href="https://fonts.googleapis.com/css2?family=Rubik:ital,wght@0,500;0,600;1,400&family=Roboto+Condensed:wght@400&display=swap">
<style>
  :root {
    --page-bg: #e8e8e8;
    --card-bg: #f7f7f7;
    --brand-dark: #3d5f67;
    --brand-deep: #477077;
    --brand-light: #6ba8b2;
    --text-main: #3a3a3a;
    --text-soft: #555;
    --card-shadow: 0 3px 6px rgba(0,0,0,0.28);
  }
  * { box-sizing: border-box; margin: 0; padding: 0; }
  html, body { width: 1200px; height: 576px; overflow: hidden; background: var(--page-bg); }
  .stage { position: relative; width: 1200px; height: 576px; }

  .card {
    position: absolute;
    top: 138px;
    width: 484px;
    height: 294px;
    background: var(--card-bg);
    border-radius: 14px;
    box-shadow: var(--card-shadow);
    overflow: hidden;
  }
  .card--front { left: 82px; }
  .card--back { left: 602px; width: 482px; }

  .brand-name {
    font-family: "Rubik", sans-serif;
    font-weight: 500;
    color: var(--brand-deep);
    white-space: nowrap;
    display: flex;
    align-items: center;
    gap: 8px;
  }
  .brand-dot {
    display: inline-block;
    border-radius: 50%;
    background: var(--brand-light);
  }

  /* Front */
  .front-lockup { position: absolute; left: 36px; top: 128px; }
  .front-lockup .brand-name { font-size: 27px; }
  .front-lockup .brand-dot { width: 20px; height: 20px; }
  .strapline {
    margin-top: 8px;
    margin-left: 28px;
    font-family: "Roboto Condensed", sans-serif;
    font-size: 9.5px;
    letter-spacing: 3px;
    color: var(--text-soft);
  }
  .strapline .divider { color: var(--brand-light); padding: 0 4px; }

  .bag-decoration {
    position: absolute;
    left: 286px;
    top: 24px;
    width: 198px;
    height: 270px;
    border-radius: 90px 0 0 0;
    background: linear-gradient(160deg, var(--brand-light) 0%, var(--brand-deep) 40%, var(--brand-dark) 100%);
  }

  /* Back */
  .holder { position: absolute; left: 22px; top: 46px; }
  .holder-name {
    font-family: "Rubik", sans-serif;
    font-weight: 600;
    font-size: 20px;
    color: var(--brand-dark);
  }
  .holder-role {
    font-family: "Rubik", sans-serif;
    font-style: italic;
    font-size: 12px;
    color: var(--text-main);
    margin-top: 2px;
  }
  .back-lockup { position: absolute; right: 20px; top: 50px; }
  .back-lockup .brand-name { font-size: 21px; }
  .back-lockup .brand-dot { width: 16px; height: 16px; }

  .bag-decoration--faint {
    left: 300px;
    top: 98px;
    width: 182px;
    height: 196px;
    border-radius: 80px 0 0 0;
    opacity: 0.35;
  }

  .address {
    position: absolute;
    left: 26px;
    top: 154px;
    font-family: "Roboto Condensed", sans-serif;
    font-size: 12.5px;
    line-height: 18px;
    color: var(--text-main);
  }
  .contact-list {
    position: absolute;
    left: 24px;
    top: 206px;
    list-style: none;
    font-family: "Roboto Condensed", sans-serif;
    font-size: 12.5px;
    color: var(--text-main);
  }
  .contact-list li { display: flex; align-items: center; height: 18.5px; }
  .contact-icon { width: 11px; height: 11px; margin-right: 12px; fill: var(--brand-deep); }
</style>
</head>
<body>
<main class="stage">

  <section class="card card--front" aria-label="Card front">
    <div class="front-lockup">
      <div class="brand-name"><span class="brand-dot"></span>BrightNestMums</div>
      <p class="strapline">TAP<span class="divider">|</span>GATHER<span class="divider">|</span>SORTED</p>
    </div>
    <div class="bag-decoration" role="img" aria-label="Large brand shopping-bag emblem in teal tones"></div>
  </section>

  <section class="card card--back" aria-label="Card back">
    <div class="holder">
      <h1 class="holder-name">Lena Forbisher</h1>
      <p class="holder-role">Founder</p>
    </div>
    <div class="back-lockup">
      <div class="brand-name"><span class="brand-dot"></span>BrightNestMums</div>
    </div>
    <div class="bag-decoration bag-decoration--faint" role="img" aria-label="Faint brand shopping-bag emblem"></div>

    <address class="address" style="font-style:normal">
      47 Kowhai Terrace, Ellerslie,<br>
      Auckland 1051, New Zealand
    </address>

    <ul class="contact-list">
      <li>
        <svg class="contact-icon" viewBox="0 0 12 12" aria-hidden="true"><path d="M3 0h6a1 1 0 0 1 1 1v10a1 1 0 0 1-1 1H3a1 1 0 0 1-1-1V1a1 1 0 0 1 1-1zm0 1.5v7.5h6V1.5zm3 8.3a.7.7 0 1 0 0 1.4.7.7 0 0 0 0-1.4z"/></svg>
        021 483 517
      </li>
      <li>
        <svg class="contact-icon" viewBox="0 0 12 12" aria-hidden="true"><path d="M1 4c0-1.5 2-2.5 5-2.5S11 2.5 11 4v1H8.5V4h-5v1H1zm2 2h6l1.5 5h-9zm3 1.2a1.3 1.3 0 1 0 0 2.6 1.3 1.3 0 0 0 0-2.6z"/></svg>
        +64 (0)9 571 4860
      </li>
      <li>
        <svg class="contact-icon" viewBox="0 0 12 12" aria-hidden="true"><path d="M0 2h12v8H0zm1 1v.3l5 3.4 5-3.4V3zm0 1.5V9h10V4.5L6 8z"/></svg>
        www.BrightNestMums.example
      </li>
      <li>
        <svg class="contact-icon" viewBox="0 0 12 12" aria-hidden="true"><path d="M6 0a6 6 0 1 1 0 12A6 6 0 0 1 6 0zm-.6 1.1C4.5 2.2 4 3.8 3.9 5.5h1.5zm1.2 0v4.4h1.5C8 3.8 7.5 2.2 6.6 1.1zM1.1 5.5h1.8c.1-1.6.5-3 1.2-4a5 5 0 0 0-3 4zm6.8-4c.7 1 1.1 2.4 1.2 4h1.8a5 5 0 0 0-3-4zM1.1 6.5a5 5 0 0 0 3 4c-.7-1-1.1-2.4-1.2-4zm2.8 0c.1 1.7.6 3.3 1.5 4.4V6.5zm2.7 0v4.4c.9-1.1 1.4-2.7 1.5-4.4zm2.5 0c-.1 1.6-.5 3-1.2 4a5 5 0 0 0 3-4z"/></svg>
        lena@brightnestmums.example
      </li>
    </ul>
  </section>

</main>
</body>
</html>
```